Fabrication and machining company needing printed material designs.

Heron Vessels, Inc. wants to use appealing visuals as well as informative text to tell potential clients about our capabilities in fabrication and machining. We have a new logo to showcase as well as a new website. The use of print media will allow us to leave tangible information with clients, and therefore the design will need to be concise, informative, and visually appealing.

Full Page Flyer (approx. 8.5" x 11"), front and back design. This will be a detailed offering of capabilities and services for our shop.

Half Page Flyer (approx. 5.5" x 8.5"), front and back design. An abbreviated version of the full page flyer, meant to be easily handed out and stored inside a note book.

Bi-fold business card front and back. General offerings of our services. Minimal if any details. Finished size is twice the size of a business card (approx. 4" x 3.5"), once folded in half will be the same size as a standard business card (approx. 2" x 3.5").

Please use www.heronvesselsinc.example for theme ideas. The font used for our logo is ethnocentric, not to be used for all text.

Target Market(s)

Industrial Consumers

Font styles to use
Sans Serif

```html
<!DOCTYPE html>
<html lang="en">
<head>
<meta charset="utf-8">
<title>Heron Vessels, Inc. — Print Collateral</title>
<link rel="stylesheet" href="https://fonts.googleapis.com/css2?family=Michroma&family=Montserrat:wght@400;500;600;700;800&display=swap">
<style>
:root{
  --orange:#f26722;
  --orange-deep:#d9541a;
  --ink:#0f0f0f;
  --char:#1c1c1c;
  --panel:#dedede;
  --chip:#bdbdbd;
  --copy:#666;
  --dark-copy:#333;
  --stage:#cfc4b0;
  --label:#3a3a3a;
}
html,body{margin:0;padding:0;width:1200px;height:3000px;overflow:hidden;background:var(--stage);font-family:'Montserrat',sans-serif}
.canvas{position:relative;width:1200px;height:3000px}
.frame{position:absolute}
.frame-label{position:absolute;width:400px;text-align:center;font:500 22px 'Montserrat',sans-serif;color:var(--label);letter-spacing:1px}

/* ---------- sheet shared ---------- */
.sheet{position:absolute;left:0;top:0;width:540px;height:699px;background:#fff;overflow:hidden;box-shadow:0 6px 18px rgba(0,0,0,.18);transform-origin:0 0}
.size-2 .sheet{transform:scale(.926)}
.brand{display:flex;align-items:center;gap:7px;font:800 12px 'Montserrat',sans-serif;letter-spacing:.6px;color:var(--ink)}
.brand-mark{width:14px;height:14px;background:var(--ink);display:block}
.brand.light{color:#fff}
.brand.light .brand-mark{background:#fff}
.photo{position:absolute}
.michroma{font-family:'Michroma',sans-serif}

.item{margin:0 0 9px}
.item h4{margin:0;color:var(--orange);font:700 10.5px/1.15 'Montserrat',sans-serif;text-transform:uppercase;letter-spacing:.2px}
.item p{margin:1px 0 0;font:500 7.5px/1.35 'Montserrat',sans-serif;color:var(--copy)}

.check-list{list-style:none;margin:0;padding:0}
.check-list li{position:relative;padding-left:16px;font:600 8.5px/1.25 'Montserrat',sans-serif;margin:0 0 9px;color:var(--dark-copy)}
.check-list li::before{content:"";position:absolute;left:0;top:1px;width:9px;height:9px;border:1.2px solid var(--orange);border-radius:50%;box-sizing:border-box}
.check-list li::after{content:"";position:absolute;left:3px;top:3.4px;width:3.4px;height:1.8px;border-left:1.2px solid var(--orange);border-bottom:1.2px solid var(--orange);transform:rotate(-45deg)}

/* ---------- flyer front ---------- */
.flyer-front .brand{position:absolute;left:26px;top:20px}
.hero-laser{left:0;top:55px;width:540px;height:180px;background:radial-gradient(ellipse at 62% 45%,#ffb36b 0,#d2601f 7%,#6a2a10 22%,#1e1410 45%,#0b0b0b 70%)}
.hero-title{position:absolute;left:40px;top:98px;margin:0;font:400 19px/1.25 'Michroma',sans-serif;color:#fff;letter-spacing:.5px}
.hero-title span{display:block}
.hero-title .accent{color:var(--orange)}
.swoosh{position:absolute;left:0;top:150px}
.cert-badge{position:absolute;left:38px;top:168px;width:112px;height:112px;border-radius:50%;background:#fff;border:6px solid #bcbcbc;box-sizing:border-box;display:flex;align-items:center;justify-content:center}
.cert-badge span{width:58px;height:58px;border-radius:50%;background:var(--char)}
.section-band{position:absolute;left:200px;right:0;top:236px;height:34px;background:var(--orange);color:#fff;font:400 17px/34px 'Michroma',sans-serif;text-align:center;letter-spacing:1px}
.cap-col{position:absolute}
.col-a{left:30px;top:292px;width:150px}
.col-b{left:190px;top:292px;width:170px}
.services-panel{position:absolute;left:376px;top:288px;width:140px;height:188px;background:var(--panel);border-radius:6px;padding:30px 12px 0;box-sizing:border-box}
.services-pill{position:absolute;left:-8px;top:10px;background:var(--orange);color:#fff;font:600 9px/18px 'Montserrat',sans-serif;padding:0 12px;border-radius:3px;letter-spacing:.4px}
.col-c{left:382px;top:492px;width:130px}
.shop-photo{left:30px;top:588px;width:150px;height:66px;background:linear-gradient(110deg,#2a2a2a 0,#7d7d7d 35%,#c9c9c9 50%,#555 70%,#1d1d1d 100%)}
.sheet-foot{position:absolute;left:0;right:0;bottom:0;height:42px;background:var(--ink)}
.foot-wedge{position:absolute;left:0;top:-10px;width:150px;height:52px;background:linear-gradient(180deg,#e6e6e6,#9c9c9c);clip-path:polygon(0 0,100% 0,84% 100%,0 100%)}
.foot-call{position:absolute;left:170px;top:7px;color:#fff}
.foot-call small{display:block;color:var(--orange);font:600 6.5px 'Montserrat',sans-serif;letter-spacing:.5px}
.foot-call strong{font:600 14px 'Montserrat',sans-serif;letter-spacing:.5px}
.foot-contact{position:absolute;left:300px;top:7px;color:#fff;font:500 7px/1.4 'Montserrat',sans-serif}
.foot-contact div{display:flex;align-items:center;gap:4px}
.foot-contact svg{flex:none}

/* ---------- flyer back ---------- */
.hero-weld{left:0;top:0;width:540px;height:250px;background:radial-gradient(ellipse at 18% 55%,#bfe3ff 0,#3d7fc4 10%,#1b2f4a 26%,#121212 52%,#080808 80%)}
.hero-edge{position:absolute;left:0;right:0;top:248px;height:4px;background:var(--orange)}
.industry-map{position:absolute;left:0;top:0}
.products{position:absolute;left:25px;top:268px;width:250px}
.products h3{margin:0 0 10px;color:var(--orange);font:800 17px 'Montserrat',sans-serif;letter-spacing:.6px}
.products .check-list li{font:700 8px/1.25 'Montserrat',sans-serif;text-transform:uppercase;margin-bottom:8px}
.roofs{margin:4px 0 10px;font:600 9px 'Montserrat',sans-serif;color:var(--dark-copy)}
.standards{display:flex;gap:0;background:var(--chip);border-radius:2px;width:210px}
.standards span{flex:1;text-align:center;font:700 7px/16px 'Montserrat',sans-serif;color:#333;border-right:1px solid #fff}
.standards span:last-child{border-right:0}
.tagline{margin:12px 0 3px;color:var(--orange);font:700 9px 'Montserrat',sans-serif}
.blurb{margin:0;width:215px;font:500 7px/1.4 'Montserrat',sans-serif;color:var(--copy)}
.orange-panel{position:absolute;left:396px;top:262px;width:144px;bottom:42px;background:linear-gradient(160deg,var(--orange),var(--orange-deep))}
.panel-title{position:absolute;right:18px;bottom:40px;writing-mode:vertical-rl;transform:rotate(180deg);margin:0;color:#fff;font:400 21px/1.3 'Michroma',sans-serif}
.panel-title span{display:block}
.part-photo{left:300px;width:120px;height:92px;border:2px solid #fff;box-sizing:border-box}
.part-1{top:280px;background:linear-gradient(135deg,#eee,#9a9a9a 50%,#dcdcdc)}
.part-2{top:384px;background:linear-gradient(135deg,#2a2a2a,#8a5a3a 45%,#c7c7c7)}
.part-3{top:488px;background:linear-gradient(135deg,#d4d4d4,#7b7b7b 55%,#e6e6e6)}
.flyer-back .foot-wedge{width:160px}
.flyer-back .foot-wedge .brand{position:absolute;left:14px;top:22px;font-size:9px}
.flyer-back .foot-wedge .brand-mark{width:11px;height:11px}

/* ---------- business card ---------- */
.card-frame{width:468px;height:410px}
.card{position:absolute;left:29px;top:-29px;width:410px;height:468px;overflow:hidden;box-shadow:0 6px 18px rgba(0,0,0,.2)}
.card-outside{background:var(--ink);transform:rotate(90deg)}
.card-inside{background:#fff;transform:rotate(-90deg)}
.card-photo{left:0;top:0;width:410px;height:234px;background:radial-gradient(ellipse at 55% 70%,#cfe9ff 0,#3a78bf 9%,#18273d 26%,#101010 55%,#070707 85%)}
.card-map{position:absolute;left:0;top:0}
.card-brand{position:absolute;left:0;right:0;top:268px;display:flex;justify-content:center;align-items:center;gap:12px;font:800 19px 'Montserrat',sans-serif;color:#fff;letter-spacing:.8px}
.card-brand i{width:34px;height:34px;background:#fff;display:block}
.card-contact{position:absolute;left:78px;top:326px;color:#fff;font:500 9px/1.6 'Montserrat',sans-serif}
.card-contact div{display:flex;align-items:center;gap:6px}
.card-call{position:absolute;left:78px;top:378px;color:#fff}
.card-call small{display:block;color:var(--orange);font:600 10px 'Montserrat',sans-serif;letter-spacing:.6px}
.card-call strong{font:600 20px 'Montserrat',sans-serif;letter-spacing:.6px}
.card-stripes{position:absolute;left:0;right:0;bottom:0;height:26px;background:linear-gradient(180deg,var(--orange) 0 3px,transparent 3px 8px,#d9d9d9 8px 12px,transparent 12px 16px,#8d8d8d 16px)}

.fold{position:absolute;left:0;right:0;top:234px;height:0;border-top:1px dashed #cfcfcf}
.in-caps{position:absolute;left:18px;top:16px;width:230px}
.in-caps h3,.in-products h3{margin:0 0 8px;color:var(--orange);font:800 14px 'Montserrat',sans-serif;letter-spacing:.6px}
.mini-list{list-style:none;margin:0;padding:0;columns:2;column-gap:12px}
.mini-list li{font:600 7.5px/1.3 'Montserrat',sans-serif;color:var(--dark-copy);text-transform:uppercase;margin:0 0 6px;break-inside:avoid}
.specialties{position:absolute;left:258px;top:16px;width:134px;height:200px;background:var(--panel);border-radius:5px;padding:30px 10px 0;box-sizing:border-box}
.specialties .services-pill{left:-6px;top:8px;font-size:8px;line-height:16px}
.specialties .mini-list{columns:1}
.in-products{position:absolute;left:18px;top:252px;width:200px}
.in-products .check-list li,.in-services .check-list li{font:700 7.5px/1.25 'Montserrat',sans-serif;text-transform:uppercase;margin-bottom:7px}
.in-services{position:absolute;left:220px;top:252px;width:172px}
.in-services h3{margin:0 0 8px;color:var(--orange);font:700 10px 'Montserrat',sans-serif;letter-spacing:.4px}
.in-services .check-list li{text-transform:none;font-size:8px}
.in-standards{position:absolute;left:18px;top:408px;width:180px}
.in-site{position:absolute;left:220px;top:414px;font:500 7.5px 'Montserrat',sans-serif;color:var(--copy)}
.in-brand{position:absolute;left:220px;top:436px;font-size:10px}
.in-brand .brand-mark{width:11px;height:11px}
.business-label{position:absolute;left:498px;top:2110px;width:204px;text-align:center;font:500 20px 'Montserrat',sans-serif;color:var(--label);letter-spacing:1px}
</style>
</head>
<body>
<main class="canvas">

  <!-- ===== Size 1 ===== -->
  <section class="frame size-1" style="left:45px;top:160px;width:540px;height:699px">
    <article class="sheet flyer-front">
      <div class="brand"><span class="brand-mark"></span>HERON VESSELS, INC.</div>
      <div class="photo hero-laser" role="img" aria-label="Laser cutter throwing orange sparks across a steel plate"></div>
      <h2 class="hero-title"><span class="accent">FABRICATION</span><span>AND MACHINING</span></h2>
      <svg class="swoosh" width="270" height="160" viewBox="0 0 270 160" aria-hidden="true"><path d="M0 70 Q90 20 230 84 L226 92 Q90 34 0 92Z" fill="#c9c9c9"/></svg>
      <div class="cert-badge" role="img" aria-label="Quality certification badge"><span></span></div>
      <div class="section-band">CAPABILITIES</div>

      <div class="cap-col col-a">
        <div class="item"><h4>Horizontal Lathes</h4><p>Up To 24" Dia &amp; 10' Long</p></div>
        <div class="item"><h4>Vertical Lathes</h4><p>Up To 44" Dia</p></div>
        <div class="item"><h4>Horizontal Boring Mill Capabilities</h4></div>
        <div class="item"><h4>Press Brake</h4><p>1" Plate x 5' Wide<br>3/8" Plate x 14' Wide</p></div>
        <div class="item"><h4>Iron Workers</h4><p>Up To 85 Tons</p></div>
        <div class="item"><h4>CNC Plasma Cutting</h4><p>8' X 20' Capacity</p></div>
        <div class="item"><h4>CNC Roll Forming</h4><p>1/2" X 10' Capacity</p></div>
      </div>
      <div class="photo shop-photo" role="img" aria-label="Machined steel shaft turning in a lathe"></div>

      <div class="cap-col col-b">
        <div class="item"><h4>Facility</h4><p>35,000 ft² Facility<br>5 Acre Storage Yard</p></div>
        <div class="item"><h4>Design &amp; Engineering</h4><p>CAD Drawings<br>Engineering Services<br>3D Modeling</p></div>
        <div class="item"><h4>Welding Processes</h4><p>Carbon Steel<br>Stainless Steel<br>Aluminum</p></div>
        <div class="item"><h4>Paint &amp; Corrosion Control</h4><p>Indoor 6500ft² Paint Bay<br>Plural Component Application Equip<br>Multi Step Liner Systems<br>Stainless Steel Passivation<br>Powder Coating<br>Galvanizing<br>Poly unc</p></div>
        <div class="item"><h4>Sandblasting</h4><p>High Production Capacity</p></div>
        <div class="item"><h4>Insulating Systems</h4><p>Polyurethane Spray Foam<br>Metal Wrap<br>Heat Trace</p></div>
      </div>

      <div class="services-panel">
        <div class="services-pill">CLIENT SERVICES</div>
        <ul class="check-list">
          <li>Custom Design</li><li>Engineering &amp; CAD Design</li><li>Quick Turn Around</li><li>Short Lead Times</li><li>Site Layout</li><li>Pipe System Design</li>
        </ul>
      </div>
      <div class="cap-col col-c">
        <div class="item"><h4>Hydraulic Assemblies</h4><p>System Testing<br>Hose Assemblies<br>Ram Rebuilding</p></div>
      </div>

      <footer class="sheet-foot">
        <div class="foot-wedge"></div>
        <div class="foot-call"><small>CALL US NOW</small><strong>555-014-2290</strong></div>
        <div class="foot-contact">
          <div><svg width="7" height="8" viewBox="0 0 7 8"><path d="M3.5 0a3 3 0 0 1 3 3c0 2-3 5-3 5S.5 5 .5 3a3 3 0 0 1 3-3z" fill="#f26722"/></svg>410 FOUNDRY ROAD, MILLBROOK, UT 84000</div>
          <div><svg width="7" height="7" viewBox="0 0 7 7"><circle cx="3.5" cy="3.5" r="3" fill="#f26722"/></svg>www.heronvesselsinc.example</div>
          <div><svg width="7" height="7" viewBox="0 0 7 7"><circle cx="3.5" cy="3.5" r="3" fill="#f26722"/></svg>sales@heronvesselsinc.example</div>
        </div>
      </footer>
    </article>
  </section>
  <div class="frame-label" style="left:115px;top:885px">SIZE 1(FRONT)</div>

  <section class="frame size-1" style="left:615px;top:160px;width:540px;height:699px">
    <article class="sheet flyer-back">
      <div class="photo hero-weld" role="img" aria-label="Welder at work with a blue arc flash in a dark shop"></div>
      <svg class="industry-map" width="540" height="250" viewBox="0 0 540 250" aria-hidden="true">
        <ellipse cx="370" cy="110" rx="115" ry="70" fill="none" stroke="#fff" stroke-width="1.2" stroke-dasharray="3 4"/>
        <rect x="330" y="80" width="80" height="40" rx="3" fill="#7d7d7d" role="img" aria-label="Storage tank farm"/>
        <text x="370" y="136" fill="#fff" font-family="Montserrat" font-weight="700" font-size="7" text-anchor="middle">HERON VESSELS</text>
        <g fill="#141414" stroke="#fff" stroke-width="1.2">
          <circle cx="275" cy="62" r="10"/><circle cx="470" cy="48" r="10"/><circle cx="478" cy="140" r="10"/><circle cx="270" cy="150" r="10"/><circle cx="372" cy="182" r="10"/>
        </g>
        <g fill="#fff"><circle cx="275" cy="62" r="3"/><circle cx="470" cy="48" r="3"/><circle cx="478" cy="140" r="3"/><circle cx="270" cy="150" r="3"/><circle cx="372" cy="182" r="3"/></g>
        <g fill="#fff" font-family="Montserrat" font-weight="700" font-size="6.5" text-anchor="middle">
          <text x="275" y="84">OIL &amp; GAS</text>
          <text x="470" y="70">POWER</text><text x="470" y="78">GENERATION</text>
          <text x="478" y="162">AGGREGATE</text>
          <text x="270" y="172">WATER &amp;</text><text x="270" y="180">WASTE WATER</text>
          <text x="372" y="204">MINING</text>
        </g>
      </svg>
      <div class="hero-edge"></div>

      <div class="orange-panel"><h2 class="panel-title"><span>FABRICATION</span><span>AND MACHINING</span></h2></div>
      <div class="photo part-photo part-1" role="img" aria-label="Stack of machined steel pipe fittings"></div>
      <div class="photo part-photo part-2" role="img" aria-label="Large threaded shaft on a lathe"></div>
      <div class="photo part-photo part-3" role="img" aria-label="Polished machined steel components"></div>

      <div class="products">
        <h3>PRODUCTS</h3>
        <ul class="check-list">
          <li>Storage Tanks,<br>Bins, Silos</li><li>Piping</li><li>Machining &amp; Assembly</li><li>Structural</li><li>Protective Coatings</li><li>Insulation</li>
        </ul>
        <p class="roofs">Internal Floating Roofs</p>
        <div class="standards"><span>API 12F</span><span>API 620</span><span>API 650</span><span>AWWA</span></div>
        <p class="tagline">A BRILLIANT IDEA MATERIALIZED...</p>
        <p class="blurb">Every great vessel starts with a bright plan. At Heron, we turn that plan into steel, from first sketch to final weld, built to serve for the long haul.</p>
      </div>

      <footer class="sheet-foot">
        <div class="foot-wedge"><div class="brand"><span class="brand-mark"></span>HERON VESSELS, INC.</div></div>
        <div class="foot-call"><small>CALL US NOW</small><strong>555-014-2290</strong></div>
        <div class="foot-contact">
          <div><svg width="7" height="8" viewBox="0 0 7 8"><path d="M3.5 0a3 3 0 0 1 3 3c0 2-3 5-3 5S.5 5 .5 3a3 3 0 0 1 3-3z" fill="#f26722"/></svg>410 FOUNDRY ROAD, MILLBROOK, UT 84000</div>
          <div><svg width="7" height="7" viewBox="0 0 7 7"><circle cx="3.5" cy="3.5" r="3" fill="#f26722"/></svg>www.heronvesselsinc.example</div>
          <div><svg width="7" height="7" viewBox="0 0 7 7"><circle cx="3.5" cy="3.5" r="3" fill="#f26722"/></svg>sales@heronvesselsinc.example</div>
        </div>
      </footer>
    </article>
  </section>
  <div class="frame-label" style="left:685px;top:885px">SIZE 1(BACK)</div>

  <!-- ===== Size 2 ===== -->
  <section class="frame size-2" style="left:65px;top:1060px;width:500px;height:647px">
    <article class="sheet flyer-front">
      <div class="brand"><span class="brand-mark"></span>HERON VESSELS, INC.</div>
      <div class="photo hero-laser" role="img" aria-label="Laser cutter throwing orange sparks across a steel plate"></div>
      <h2 class="hero-title"><span class="accent">FABRICATION</span><span>AND MACHINING</span></h2>
      <svg class="swoosh" width="270" height="160" viewBox="0 0 270 160" aria-hidden="true"><path d="M0 70 Q90 20 230 84 L226 92 Q90 34 0 92Z" fill="#c9c9c9"/></svg>
      <div class="cert-badge" role="img" aria-label="Quality certification badge"><span></span></div>
      <div class="section-band">CAPABILITIES</div>
      <div class="cap-col col-a">
        <div class="item"><h4>Horizontal Lathes</h4><p>Up To 24" Dia &amp; 10' Long</p></div>
        <div class="item"><h4>Vertical Lathes</h4><p>Up To 44" Dia</p></div>
        <div class="item"><h4>Horizontal Boring Mill Capabilities</h4></div>
        <div class="item"><h4>Press Brake</h4><p>1" Plate x 5' Wide<br>3/8" Plate x 14' Wide</p></div>
        <div class="item"><h4>Iron Workers</h4><p>Up To 85 Tons</p></div>
        <div class="item"><h4>CNC Plasma Cutting</h4><p>8' X 20' Capacity</p></div>
        <div class="item"><h4>CNC Roll Forming</h4><p>1/2" X 10' Capacity</p></div>
      </div>
      <div class="photo shop-photo" role="img" aria-label="Machined steel shaft turning in a lathe"></div>
      <div class="cap-col col-b">
        <div class="item"><h4>Facility</h4><p>35,000 ft² Facility<br>5 Acre Storage Yard</p></div>
        <div class="item"><h4>Design &amp; Engineering</h4><p>CAD Drawings<br>Engineering Services<br>3D Modeling</p></div>
        <div class="item"><h4>Welding Processes</h4><p>Carbon Steel<br>Stainless Steel<br>Aluminum</p></div>
        <div class="item"><h4>Paint &amp; Corrosion Control</h4><p>Indoor 6500ft² Paint Bay<br>Plural Component Application Equip<br>Multi Step Liner Systems<br>Stainless Steel Passivation<br>Powder Coating<br>Galvanizing<br>Poly unc</p></div>
        <div class="item"><h4>Sandblasting</h4><p>High Production Capacity</p></div>
        <div class="item"><h4>Insulating Systems</h4><p>Polyurethane Spray Foam<br>Metal Wrap<br>Heat Trace</p></div>
      </div>
      <div class="services-panel">
        <div class="services-pill">CLIENT SERVICES</div>
        <ul class="check-list">
          <li>Custom Design</li><li>Engineering &amp; CAD Design</li><li>Quick Turn Around</li><li>Short Lead Times</li><li>Site Layout</li><li>Pipe System Design</li>
        </ul>
      </div>
      <div class="cap-col col-c">
        <div class="item"><h4>Hydraulic Assemblies</h4><p>System Testing<br>Hose Assemblies<br>Ram Rebuilding</p></div>
      </div>
      <footer class="sheet-foot">
        <div class="foot-wedge"></div>
        <div class="foot-call"><small>CALL US NOW</small><strong>555-014-2290</strong></div>
        <div class="foot-contact">
          <div><svg width="7" height="8" viewBox="0 0 7 8"><path d="M3.5 0a3 3 0 0 1 3 3c0 2-3 5-3 5S.5 5 .5 3a3 3 0 0 1 3-3z" fill="#f26722"/></svg>410 FOUNDRY ROAD, MILLBROOK, UT 84000</div>
          <div><svg width="7" height="7" viewBox="0 0 7 7"><circle cx="3.5" cy="3.5" r="3" fill="#f26722"/></svg>www.heronvesselsinc.example</div>
          <div><svg width="7" height="7" viewBox="0 0 7 7"><circle cx="3.5" cy="3.5" r="3" fill="#f26722"/></svg>sales@heronvesselsinc.example</div>
        </div>
      </footer>
    </article>
  </section>
  <div class="frame-label" style="left:115px;top:1735px">SIZE 2(FRONT)</div>

  <section class="frame size-2" style="left:635px;top:1060px;width:500px;height:647px">
    <article class="sheet flyer-back">
      <div class="photo hero-weld" role="img" aria-label="Welder at work with a blue arc flash in a dark shop"></div>
      <svg class="industry-map" width="540" height="250" viewBox="0 0 540 250" aria-hidden="true">
        <ellipse cx="370" cy="110" rx="115" ry="70" fill="none" stroke="#fff" stroke-width="1.2" stroke-dasharray="3 4"/>
        <rect x="330" y="80" width="80" height="40" rx="3" fill="#7d7d7d"/>
        <text x="370" y="136" fill="#fff" font-family="Montserrat" font-weight="700" font-size="7" text-anchor="middle">HERON VESSELS</text>
        <g fill="#141414" stroke="#fff" stroke-width="1.2">
          <circle cx="275" cy="62" r="10"/><circle cx="470" cy="48" r="10"/><circle cx="478" cy="140" r="10"/><circle cx="270" cy="150" r="10"/><circle cx="372" cy="182" r="10"/>
        </g>
        <g fill="#fff"><circle cx="275" cy="62" r="3"/><circle cx="470" cy="48" r="3"/><circle cx="478" cy="140" r="3"/><circle cx="270" cy="150" r="3"/><circle cx="372" cy="182" r="3"/></g>
        <g fill="#fff" font-family="Montserrat" font-weight="700" font-size="6.5" text-anchor="middle">
          <text x="275" y="84">OIL &amp; GAS</text>
          <text x="470" y="70">POWER</text><text x="470" y="78">GENERATION</text>
          <text x="478" y="162">AGGREGATE</text>
          <text x="270" y="172">WATER &amp;</text><text x="270" y="180">WASTE WATER</text>
          <text x="372" y="204">MINING</text>
        </g>
      </svg>
      <div class="hero-edge"></div>
      <div class="orange-panel"><h2 class="panel-title"><span>FABRICATION</span><span>AND MACHINING</span></h2></div>
      <div class="photo part-photo part-1" role="img" aria-label="Stack of machined steel pipe fittings"></div>
      <div class="photo part-photo part-2" role="img" aria-label="Large threaded shaft on a lathe"></div>
      <div class="photo part-photo part-3" role="img" aria-label="Polished machined steel components"></div>
      <div class="products">
        <h3>PRODUCTS</h3>
        <ul class="check-list">
          <li>Storage Tanks,<br>Bins, Silos</li><li>Piping</li><li>Machining &amp; Assembly</li><li>Structural</li><li>Protective Coatings</li><li>Insulation</li>
        </ul>
        <p class="roofs">Internal Floating Roofs</p>
        <div class="standards"><span>API 12F</span><span>API 620</span><span>API 650</span><span>AWWA</span></div>
        <p class="tagline">A BRILLIANT IDEA MATERIALIZED...</p>
        <p class="blurb">Every great vessel starts with a bright plan. At Heron, we turn that plan into steel, from first sketch to final weld, built to serve for the long haul.</p>
      </div>
      <footer class="sheet-foot">
        <div class="foot-wedge"><div class="brand"><span class="brand-mark"></span>HERON VESSELS, INC.</div></div>
        <div class="foot-call"><small>CALL US NOW</small><strong>555-014-2290</strong></div>
        <div class="foot-contact">
          <div><svg width="7" height="8" viewBox="0 0 7 8"><path d="M3.5 0a3 3 0 0 1 3 3c0 2-3 5-3 5S.5 5 .5 3a3 3 0 0 1 3-3z" fill="#f26722"/></svg>410 FOUNDRY ROAD, MILLBROOK, UT 84000</div>
          <div><svg width="7" height="7" viewBox="0 0 7 7"><circle cx="3.5" cy="3.5" r="3" fill="#f26722"/></svg>www.heronvesselsinc.example</div>
          <div><svg width="7" height="7" viewBox="0 0 7 7"><circle cx="3.5" cy="3.5" r="3" fill="#f26722"/></svg>sales@heronvesselsinc.example</div>
        </div>
      </footer>
    </article>
  </section>
  <div class="frame-label" style="left:685px;top:1735px">SIZE 2(BACK)</div>

  <!-- ===== Size 3 — bi-fold business card ===== -->
  <section class="frame card-frame" style="left:30px;top:1920px">
    <article class="card card-outside">
      <div class="photo card-photo" role="img" aria-label="Welder grinding steel with blue sparks in a dark shop"></div>
      <svg class="card-map" width="410" height="234" viewBox="0 0 410 234" aria-hidden="true">
        <ellipse cx="240" cy="95" rx="110" ry="62" fill="none" stroke="#fff" stroke-width="1" stroke-dasharray="3 4"/>
        <rect x="208" y="74" width="64" height="34" rx="3" fill="#7d7d7d"/>
        <g fill="#141414" stroke="#fff" stroke-width="1"><circle cx="150" cy="55" r="9"/><circle cx="330" cy="50" r="9"/><circle cx="345" cy="120" r="9"/><circle cx="140" cy="135" r="9"/><circle cx="245" cy="158" r="9"/></g>
        <g fill="#fff" font-family="Montserrat" font-weight="700" font-size="6" text-anchor="middle">
          <text x="150" y="75">OIL &amp; GAS</text><text x="330" y="70">POWER GEN</text><text x="345" y="140">AGGREGATE</text><text x="140" y="155">WATER</text><text x="245" y="178">MINING</text>
        </g>
      </svg>
      <div class="card-brand"><i></i>HERON VESSELS, INC.</div>
      <div class="card-contact">
        <div><svg width="8" height="9" viewBox="0 0 7 8"><path d="M3.5 0a3 3 0 0 1 3 3c0 2-3 5-3 5S.5 5 .5 3a3 3 0 0 1 3-3z" fill="#f26722"/></svg>410 FOUNDRY ROAD, MILLBROOK, UT 84000</div>
        <div><svg width="8" height="8" viewBox="0 0 7 7"><circle cx="3.5" cy="3.5" r="3" fill="#f26722"/></svg>www.heronvesselsinc.example</div>
        <div><svg width="8" height="8" viewBox="0 0 7 7"><circle cx="3.5" cy="3.5" r="3" fill="#f26722"/></svg>sales@heronvesselsinc.example</div>
      </div>
      <div class="card-call"><small>CALL US NOW</small><strong>555-014-2290</strong></div>
      <div class="card-stripes"></div>
    </article>
  </section>
  <div class="frame-label" style="left:64px;top:2360px">SIZE 3</div>

  <div class="business-label">BUSINESS CARD</div>

  <section class="frame card-frame" style="left:702px;top:1920px">
    <article class="card card-inside">
      <div class="in-caps">
        <h3>CAPABILITIES</h3>
        <ul class="mini-list">
          <li>Horizontal Lathes</li><li>Vertical Lathes</li><li>Horizontal Boring Mill Capabilities</li><li>Press Brake</li><li>Iron Workers</li><li>CNC Plasma Cutting</li><li>CNC Roll Forming</li><li>35,000 ft² Facility</li><li>Design &amp; Engineering</li><li>Paint &amp; Corrosion Control</li><li>Sandblasting</li><li>Insulating Systems</li><li>Hydraulic Assemblies</li><li>Driveline</li>
        </ul>
      </div>
      <div class="specialties">
        <div class="services-pill">SPECIALTIES</div>
        <ul class="mini-list">
          <li>Tanks</li><li>Piping</li><li>Fireboxes</li><li>Walkways &amp; Stairs</li><li>Pump Skids</li><li>Trailer Components</li><li>Tank Vents</li><li>Clarifiers</li>
        </ul>
      </div>
      <div class="fold"></div>
      <div class="in-products">
        <h3>PRODUCTS</h3>
        <ul class="check-list">
          <li>Storage Tanks, Bins, Silos</li><li>Piping</li><li>Machining / Assembly</li><li>Structural</li><li>Protective Coatings</li><li>Insulation</li>
        </ul>
      </div>
      <div class="in-services">
        <h3>CLIENT SERVICES</h3>
        <ul class="check-list">
          <li>Custom Design</li><li>Engineering + CAD Design</li><li>Quick Turn Around</li><li>Site Layout</li><li>Short Lead Times</li><li>Pipe System Design</li>
        </ul>
      </div>
      <div class="in-standards">
        <p class="roofs">Internal Floating Roofs</p>
        <div class="standards" style="width:170px"><span>API 12F</span><span>API 620</span><span>API 650</span><span>AWWA</span></div>
      </div>
      <div class="in-site">www.heronvesselsinc.example</div>
      <div class="brand in-brand"><span class="brand-mark"></span>HERON VESSELS, INC.</div>
    </article>
  </section>
  <div class="frame-label" style="left:736px;top:2360px">SIZE 3</div>

</main>
</body>
</html>
```